Change of trading name, rebrand

existing website to be updated with new theme and logo. existing website is
www.harlowbrentmere.com.au
Industry/Entity Type
Construction
Coding
Coded - Design and coding required
Number of Pages Required
5+ page
Requirements
Must have
- be mobile phone friendly

```html
<!DOCTYPE html>
<html lang="en">
<head>
<meta charset="utf-8">
<title>HBR Plant Hire</title>
<link href="https://fonts.googleapis.com/css2?family=Bebas+Neue&family=Poppins:wght@300;400;500;600&display=swap" rel="stylesheet">
<style>
:root{
  --navy:#2b3190;
  --navy-dark:#1f2370;
  --ink:#1d1d1d;
  --text:#555;
  --grey-bg:#efefef;
  --footer:#08080d;
  --white:#fff;
}
*{box-sizing:border-box;margin:0;padding:0}
html,body{width:1200px;height:3879px;overflow:hidden;background:#fff}
body{position:relative;font-family:"Poppins",sans-serif;color:var(--ink)}
.abs{position:absolute}
.head{font-family:"Bebas Neue",sans-serif;letter-spacing:.5px}
.btn{position:absolute;display:flex;align-items:center;justify-content:center;gap:8px;font-weight:600;font-size:15px;text-transform:uppercase;border-radius:5px}
.btn .ar{width:14px;height:14px;border-radius:50%;background:currentColor;display:inline-block;position:relative}
.btn .ar::after{content:"";position:absolute;left:4px;top:4px;width:4px;height:4px;border-top:2px solid var(--navy);border-right:2px solid var(--navy);transform:rotate(45deg)}
.btn-navy{background:var(--navy);color:#fff}
.btn-outline{border:2px solid #fff;color:#fff}
.btn-outline .ar::after{border-color:#000}

.brand{left:117px;top:12px;width:180px;text-align:center}
.brand-name{font-family:"Bebas Neue",sans-serif;font-size:74px;line-height:.9;color:var(--navy)}
.brand-sub{font-weight:600;font-size:13px;letter-spacing:5px;color:#111}
.topbar{left:334px;top:0;width:866px;height:50px}
.topbar .dark{position:absolute;left:0;top:0;width:600px;height:50px;background:var(--navy-dark);clip-path:polygon(22px 0,100% 0,100% 100%,0 100%,0 26px)}
.topbar .grey{position:absolute;left:580px;top:0;width:286px;height:50px;background:#555;clip-path:polygon(20px 0,100% 0,100% 100%,0 100%)}
.contact-chip{position:absolute;top:7px;display:flex;align-items:center;gap:12px;color:#fff;font-size:13px}
.contact-chip .circ{width:36px;height:36px;border-radius:50%;border:1.5px solid #fff;display:flex;align-items:center;justify-content:center}
.quote{position:absolute;left:624px;top:15px;color:#fff;font-family:"Bebas Neue",sans-serif;font-size:17px}
.nav{left:366px;top:83px;display:flex;gap:31px;font-size:15px;color:#333}
.nav .active{background:linear-gradient(#e8eaf5,#e8eaf5) no-repeat 0 50%/100% 18px;padding:0 3px 0 20px;color:var(--navy);font-weight:600}

.hero{left:0;top:138px;width:1200px;height:742px;background:linear-gradient(90deg,#2a1c12 0%,#4b3321 40%,#8a5f3b 70%,#6b4a30 100%)}
.hero-welcome{left:111px;top:293px;font-size:46px;color:#fff}
.hero-title{left:111px;top:352px;font-size:100px;line-height:1;color:#fff}
.hero-title span{color:var(--navy);-webkit-text-stroke:1.5px #fff}
.hero-text{left:111px;top:478px;width:490px;font-size:14px;line-height:26px;color:#fff}
.slide-dots{display:flex;gap:8px}
.slide-dots i{width:12px;height:12px;border-radius:50%;background:#fff;display:block}
.slide-dots i.on{background:var(--navy);box-shadow:0 0 0 3px #fff}

.dotgrid{position:absolute;background-image:radial-gradient(var(--navy) 1.6px,transparent 1.8px);background-size:13px 13px}
.about-img1{left:111px;top:885px;width:439px;height:395px;background:linear-gradient(180deg,#7ea3cf 0%,#c8d6e6 40%,#9a6a4e 70%,#7d7b78 100%)}
.about-img2{left:366px;top:1107px;width:233px;height:211px;background:linear-gradient(180deg,#3f79c4 0%,#9fbde0 40%,#d9b33a 65%,#5a5a5a 100%);outline:7px solid #fff}
.about-title{left:667px;top:866px;font-size:44px;color:#111}
.bar{position:absolute;height:4px;background:var(--navy)}
.about-sub{left:667px;top:946px;width:420px;font-size:22px;line-height:33px;font-weight:500;color:#444}
.about-text{left:667px;top:1029px;width:416px;font-size:12.6px;line-height:24px;color:var(--text)}

.features{left:0;top:1444px;width:1200px;height:410px;background:var(--grey-bg)}
.feature{position:absolute;top:1536px;width:174px}
.feature .box{width:174px;height:158px;background:#fff;border:1px solid #e4e4e4;display:flex;align-items:center;justify-content:center}
.feature.on .box{border:1.5px solid var(--navy)}
.feature p{margin-top:22px;text-align:center;font-size:15px;line-height:26px;font-weight:500;color:#222}
.feature.on p{color:var(--navy)}

.svc{position:absolute;top:1943px;width:305px;height:467px;background:#fff;box-shadow:0 0 10px rgba(0,0,0,.08)}
.svc .ph{position:absolute;left:9px;top:9px;width:287px;height:209px}
.svc h3{position:absolute;left:20px;top:238px;font-size:25px;color:#222}
.svc p{position:absolute;left:20px;top:280px;width:262px;height:98px;overflow:hidden;font-size:12.8px;line-height:23px;color:var(--text);text-align:justify}
.svc .btn{left:20px;top:388px;width:155px;height:53px}
.arrow-c{position:absolute;top:2159px;width:38px;height:38px;border-radius:50%;border:1.5px solid #333;display:flex;align-items:center;justify-content:center}

.clients{left:0;top:2510px;width:1200px;height:359px;background:linear-gradient(90deg,#2d338f 0%,#3a3f9a 50%,#343a96 100%)}
.clients-title{left:0;top:2572px;width:1200px;text-align:center;font-size:44px;color:#fff}
.client{position:absolute;top:2676px;width:160px;height:83px;border:1.5px solid rgba(255,255,255,.8);border-radius:5px;background:rgba(255,255,255,.06);display:flex;align-items:center;justify-content:center;gap:8px;color:rgba(255,255,255,.85);font-size:20px;font-weight:600}
.client.on{border:2px solid #fff;color:#fff;background:rgba(255,255,255,.12)}
.client .sq{width:14px;height:14px;background:currentColor}
.client-dots{left:569px;top:2804px;display:flex;gap:7px}
.client-dots i{width:10px;height:10px;border-radius:50%;background:#aab;display:block}
.client-dots i.on{background:#fff;border:2px solid #aab}

.dark-band{left:0;top:3361px;width:1200px;height:518px;background:var(--footer)}
.contact{left:184px;top:2977px;width:833px;height:517px;background:var(--navy)}
.contact-title{left:184px;top:3018px;width:833px;text-align:center;font-size:44px;color:#fff}
.field{position:absolute;background:#fff;border-radius:5px;font-size:11px;color:#555;padding:21px 20px}
.submit{left:532px;top:3404px;width:135px;height:45px;border:1.5px solid #fff;font-size:13px;border-radius:6px}

.flogo{left:113px;top:3575px;width:221px;text-align:center;color:#fff}
.flogo .brand-name{color:#fff;font-size:88px}
.flogo .brand-sub{color:#fff;font-size:15px}
.social{position:absolute;top:3709px;width:36px;height:36px;border-radius:50%;background:#fff}
.social.on{background:var(--navy);border:1.5px solid #fff}
.vline{left:390px;top:3540px;width:1px;height:210px;background:#333}
.fcol{position:absolute;top:3546px;color:#fff}
.fcol h4{font-size:20px;font-weight:500;margin-bottom:12px}
.fcol li{list-style:none;font-size:14px;line-height:25.6px;padding-left:25px;position:relative}
.fcol li::before{content:"»";position:absolute;left:0;top:-1px;font-size:16px}
.fcontact{left:881px;top:3546px;color:#fff;font-size:14px;line-height:22px}
.fcontact h4{font-size:20px;font-weight:500;margin-bottom:12px}
.fcontact .row{display:flex;gap:10px;margin-bottom:14px}
.hline{left:111px;top:3788px;width:978px;height:1px;background:#333}
.copy{left:0;top:3812px;width:1200px;text-align:center;color:#fff;font-size:14px}
</style>
</head>
<body>

<div class="abs brand"><div class="brand-name">HBR</div><div class="brand-sub">PLANT HIRE</div></div>
<div class="abs topbar">
  <div class="dark"></div><div class="grey"></div>
  <div class="contact-chip" style="left:62px"><span class="circ"><svg width="16" height="16" viewBox="0 0 24 24"><path fill="#fff" d="M6.6 10.8a15 15 0 0 0 6.6 6.6l2.2-2.2c.3-.3.7-.4 1-.2 1.1.4 2.3.6 3.6.6.6 0 1 .4 1 1V20c0 .6-.4 1-1 1A17 17 0 0 1 3 4c0-.6.4-1 1-1h3.5c.6 0 1 .4 1 1 0 1.3.2 2.5.6 3.6.1.3 0 .7-.2 1z"/></svg></span><span><b>Phone:</b> 1300 555 214</span></div>
  <div class="contact-chip" style="left:280px"><span class="circ"><svg width="16" height="14" viewBox="0 0 24 20"><path fill="#fff" d="M2 2h20v16H2z M2 2l10 8 10-8" stroke="#1f2370" stroke-width="1.5"/></svg></span><span><b>Email:</b> info@harlowbrentmere.com</span></div>
  <div class="quote">GET A QUOTE &nbsp;›</div>
</div>
<nav class="abs nav">
  <span class="active">Home</span><span>About us</span><span>Plant Hire</span><span>Major Project Snapshot</span><span>Policies</span><span>Jobs</span><span>Contact us</span>
</nav>

<div class="abs hero" role="img" aria-label="Close-up of an excavator bucket digging into dusty earth"></div>
<svg class="abs" style="left:0;top:650px" width="1200" height="240" viewBox="0 0 1200 240">
  <polygon points="0,178 770,12 1200,52 1200,240 0,240" fill="var(--navy)"/>
  <polygon points="0,226 770,26 1200,70 1200,240 0,240" fill="#fff"/>
</svg>
<div class="abs head hero-welcome">WELCOME TO</div>
<div class="abs head hero-title">HBR <span>PLANT HIRE</span></div>
<p class="abs hero-text">Harlow Brentmere Heavy Equipment Hire specialise in the hire of heavy earthmoving, mining and construction machines with specialised attachments and tooling.</p>
<div class="btn btn-outline" style="left:111px;top:586px;width:154px;height:51px">Get Started <span class="ar"></span></div>
<div class="abs slide-dots" style="left:574px;top:655px"><i></i><i class="on"></i><i></i></div>

<div class="dotgrid" style="left:480px;top:862px;width:100px;height:82px"></div>
<div class="dotgrid" style="left:1115px;top:1282px;width:85px;height:80px"></div>
<div class="abs about-img1" role="img" aria-label="Excavator being lifted by crane on a wharf"></div>
<div class="abs about-img2" role="img" aria-label="Yellow excavator loaded on a low loader truck"></div>
<h2 class="abs head about-title">HBR HEAVY EQUIPMENT HIRE</h2>
<div class="bar" style="left:667px;top:924px;width:60px"></div>
<p class="abs about-sub">Committed to superior quality plant hire services.</p>
<p class="abs about-text">Harlow Brentmere Heavy Equipment Hire specialise in the hire of heavy earthmoving, mining and construction machines with specialised attachments and tooling. Our array of machines and attachments is second to none, and we have one of the largest hire fleets available in South East Queensland. If its plant hire you require, then Harlow Brentmere Resources, or HBR as the local's call us – should be the first call you make. Wet or dry hire, we provide excellent operators and quality machines across all makes and models to guarantee you maximum up-time.</p>
<div class="btn btn-navy" style="left:667px;top:1274px;width:157px;height:53px">Learn More <span class="ar" style="background:#fff"></span></div>

<div class="abs features"></div>
<div class="feature" style="left:114px"><div class="box"><svg width="90" height="90" viewBox="0 0 90 90" fill="none" stroke="#777" stroke-width="2.5"><circle cx="45" cy="50" r="18"/><circle cx="45" cy="50" r="11"/><path d="M40 50l4 4 7-8M32 64l-8 14 10-2 4 8 6-12M58 64l8 14-10-2-4 8-6-12M45 12l3 6 6 1-4 4 1 6-6-3-6 3 1-6-4-4 6-1z"/></svg></div><p>Years Of Experience</p></div>
<div class="feature" style="left:313px"><div class="box"><svg width="100" height="80" viewBox="0 0 100 80" fill="none" stroke="#777" stroke-width="3"><rect x="10" y="50" width="60" height="16" rx="8"/><path d="M15 50V36h25l8 14M48 36l20-10 16 14-6 12M84 40l6 16H74"/><circle cx="22" cy="58" r="2"/><circle cx="34" cy="58" r="2"/><circle cx="46" cy="58" r="2"/><circle cx="58" cy="58" r="2"/></svg></div><p>Machines In Fleet</p></div>
<div class="feature on" style="left:514px"><div class="box"><svg width="96" height="96" viewBox="0 0 96 96" fill="none" stroke="#2b3190" stroke-width="2.5"><circle cx="48" cy="50" r="9"/><circle cx="48" cy="50" r="15" stroke-dasharray="5 4"/><rect x="36" y="10" width="20" height="13"/><circle cx="40" cy="25" r="3"/><circle cx="54" cy="25" r="3"/><rect x="12" y="58" width="16" height="16"/><circle cx="76" cy="66" r="10"/><path d="M22 46a28 28 0 0 1 10-24M70 30a28 28 0 0 1 6 16M40 82h20"/></svg></div><p>One Of Qld's Largest Suppliers</p></div>
<div class="feature" style="left:712px"><div class="box"><svg width="90" height="90" viewBox="0 0 90 90" fill="none" stroke="#777" stroke-width="2.5"><circle cx="30" cy="30" r="12"/><path d="M45 34a14 14 0 0 1 28 0zM42 34h34M50 80V64h24v16M46 80V62a8 8 0 0 1 8-8h16a8 8 0 0 1 8 8v18"/><circle cx="59" cy="43" r="8"/></svg></div><p>Onsite Servicing</p></div>
<div class="feature" style="left:913px"><div class="box"><svg width="80" height="80" viewBox="0 0 80 80" fill="none" stroke="#777" stroke-width="3"><path d="M14 66l40-40M26 14l40 40"/><circle cx="12" cy="68" r="7"/><circle cx="68" cy="12" r="7"/><circle cx="20" cy="20" r="9"/><circle cx="62" cy="62" r="9"/></svg></div><p>Custom Machine Attachments</p></div>

<div class="dotgrid" style="left:86px;top:1918px;width:95px;height:82px"></div>
<div class="arrow-c" style="left:54px"><svg width="12" height="14"><path d="M9 1L3 7l6 6" stroke="#333" stroke-width="1.6" fill="none"/></svg></div>
<div class="arrow-c" style="left:1107px"><svg width="12" height="14"><path d="M3 1l6 6-6 6" stroke="#333" stroke-width="1.6" fill="none"/></svg></div>
<div class="svc" style="left:111px">
  <div class="ph" role="img" aria-label="Yellow water cart truck" style="background:linear-gradient(180deg,#9ec0e2 0%,#e2c44a 45%,#c9a52c 75%,#6f6b5f 100%)"></div>
  <h3 class="head">Water Cart Hire</h3>
  <p>If you need expert dust suppression services, look no further than Harlow Brentmere Resources. Our range of road-registered and</p>
  <div class="btn btn-navy">Learn More <span class="ar" style="background:#fff"></span></div>
</div>
<div class="svc" style="left:447px">
  <div class="ph" role="img" aria-label="Yellow backhoe loader parked on grass" style="background:linear-gradient(180deg,#4a86d0 0%,#9cc0e6 35%,#d9b523 60%,#3d4c2e 100%)"></div>
  <h3 class="head">Backhoe Hire</h3>
  <p>From Brisbane to Gold Coast, Toowoomba and throughout South East Queensland, HBR offers a range of high-quality backhoes for hire.</p>
  <div class="btn btn-navy">Learn More <span class="ar" style="background:#fff"></span></div>
</div>
<div class="svc" style="left:783px">
  <div class="ph" role="img" aria-label="Yellow soil compactor with padfoot drum" style="background:linear-gradient(180deg,#c9d8ea 0%,#d8b85a 40%,#a88738 70%,#8d8779 100%)"></div>
  <h3 class="head">Compactor Hire</h3>
  <p>Compactors are a rare and specialist machine with specific application and we are proud to operate a fleet of Marrick compactors for all your soil</p>
  <div class="btn btn-navy">Learn More <span class="ar" style="background:#fff"></span></div>
</div>

<div class="abs clients" role="img" aria-label="Excavator on a job site behind a navy overlay"></div>
<h2 class="abs head clients-title">OUR CLIENTS</h2>
<div class="bar" style="left:570px;top:2632px;width:60px;background:#fff"></div>
<div class="client" style="left:111px"><span class="sq"></span>Ridgeway</div>
<div class="client" style="left:316px">Kestrel</div>
<div class="client on" style="left:521px"><span class="sq"></span>Summit</div>
<div class="client" style="left:726px">Corbel</div>
<div class="client" style="left:929px">Northline</div>
<div class="abs client-dots"><i></i><i class="on"></i><i></i><i></i></div>

<div class="abs dark-band"></div>
<div class="dotgrid" style="left:955px;top:2942px;width:100px;height:82px"></div>
<div class="abs contact"></div>
<div class="dotgrid" style="left:207px;top:3355px;width:95px;height:82px;background-image:radial-gradient(#fff 1.6px,transparent 1.8px)"></div>
<h2 class="abs head contact-title">CONTACT US</h2>
<div class="bar" style="left:570px;top:3072px;width:60px;background:#fff"></div>
<div class="field" style="left:251px;top:3113px;width:338px;height:56px">First Name</div>
<div class="field" style="left:610px;top:3113px;width:337px;height:56px">Last Name</div>
<div class="field" style="left:251px;top:3194px;width:338px;height:56px">Email</div>
<div class="field" style="left:610px;top:3194px;width:337px;height:56px">Phone</div>
<div class="field" style="left:251px;top:3276px;width:694px;height:100px">Enquiry</div>
<div class="btn submit" style="color:#fff">Submit Now <span class="ar" style="background:#fff"></span></div>

<div class="abs flogo"><div class="brand-name">HBR</div><div class="brand-sub">PLANT HIRE</div></div>
<div class="social on" style="left:112px" aria-label="Social link 1"></div>
<div class="social" style="left:155px" aria-label="Social link 2"></div>
<div class="social" style="left:197px" aria-label="Social link 3"></div>
<div class="social" style="left:241px" aria-label="Social link 4"></div>
<div class="abs vline"></div>
<div class="fcol" style="left:432px"><h4>Quick Links</h4><ul><li>Home</li><li>About us</li><li>Plant Hire</li><li>Major Project Snapshot</li><li>Policies</li><li>Jobs</li><li>Contact us</li></ul></div>
<div class="fcol" style="left:658px"><h4>Our Company</h4><ul><li>Articulated Dump<br>Trucks Hire</li><li>Dozer Hire</li><li>Excavator Diggers Hire</li><li>Grader Hire</li><li>Attachments Hire</li></ul></div>
<div class="abs fcontact"><h4>Contact us</h4>
  <div class="row"><svg width="14" height="18" viewBox="0 0 14 18"><path fill="#fff" d="M7 0a7 7 0 0 0-7 7c0 5 7 11 7 11s7-6 7-11a7 7 0 0 0-7-7zm0 10a3 3 0 1 1 0-6 3 3 0 0 1 0 6z"/></svg><span>42 Banksia Rd,<br>Westmoor VIC 3999</span></div>
  <div class="row"><svg width="16" height="16" viewBox="0 0 24 24"><path fill="#fff" d="M6.6 10.8a15 15 0 0 0 6.6 6.6l2.2-2.2c.3-.3.7-.4 1-.2 1.1.4 2.3.6 3.6.6.6 0 1 .4 1 1V20c0 .6-.4 1-1 1A17 17 0 0 1 3 4c0-.6.4-1 1-1h3.5c.6 0 1 .4 1 1 0 1.3.2 2.5.6 3.6.1.3 0 .7-.2 1z"/></svg><span>1300 555 214</span></div>
  <div class="row"><svg width="16" height="14" viewBox="0 0 24 20"><rect x="1" y="2" width="22" height="16" fill="#fff"/><path d="M1 2l11 9 11-9" stroke="#08080d" stroke-width="2" fill="none"/></svg><span>info@harlowbrentmere.com</span></div>
</div>
<div class="abs hline"></div>
<p class="abs copy">©Copyrights 2024 Harlowbrentmere &nbsp;| &nbsp; All Rights Reserved</p>

</body>
</html>
```